Website for a company offering full serivce charging solutions for electric cars

The company "tanu-werk" (english: "tanu-works") offering all-in-one-solutions for charging infrastructure for electric mobility.

There are four products:
1- Wallboxes for single-family homes
2- Solutions for property devloper/-management for property parking space
3- All-in-one-charging solution for municipalities/communities
4- Solutions for tourism/hotels/holiday appartments

The Website structure:
1. Main Page
2.1. Product Page Single Homes
2.2. Product Page Property Management / Parking
2.3. Product Page Municipality
2.4. Product Page Tourism
3. Contact Form / Request for information
4. Imprint / Legal

The Website should be built on Wordpress with a powerful possibility to simply add/modify specific landing pages.

We would like you to implement the website later and also maintain it if possible, but we would be able to do minor modifications by ourselfs (for A/B-Testing)

The website should be clear and simple, easy to understand.
Target group is mainly B2C without deeper knowledge of that topic.

It should suggest, that we will provide a very simple way to get the charging infrastructure done.

We need a contact form, maybe we will use Hubspot later.

Attached you will find a draft of the main page and a landing page (for 2.2) - it is just the content, please ignore the design. We would love to let you create a suitable design.
Also you will find some drafts a bit different for the same story.

I added also a few stock photos, but they don't need to be used! If you have better ideas, you are welcome!

Industry/Entity Type

Charging/Electric mobility

Number of Pages Required

2 page

Font styles to use
Sans Serif

Requirements
Must have
• Based on Wordpress, and the designer should be able to implement it on Wordpress on a later step

```html
<!DOCTYPE html>
<html lang="de">
<head>
<meta charset="utf-8">
<title>tanu-werk.de – Lösungen</title>
<link href="https://fonts.googleapis.com/css2?family=Mulish:wght@400;500;600;700;800;900&family=Montserrat:wght@800;900&display=swap" rel="stylesheet">
<style>
:root{
  --bg:#111a2b;
  --header:#0f1626;
  --card:#172036;
  --card-inner:#1c2743;
  --line:#2a3552;
  --magenta:#d81f97;
  --violet:#9b2fd6;
  --white:#ffffff;
  --text:#e9ecf3;
  --footer:#0a0f1a;
}
*{box-sizing:border-box;margin:0;padding:0}
html,body{width:1200px;height:2332px;overflow:hidden}
body{background:var(--bg);font-family:'Mulish',sans-serif;color:var(--text);position:relative}
.site-header{position:absolute;top:0;left:0;width:1200px;height:75px;background:var(--header)}
.brand{position:absolute;display:flex;align-items:center;gap:9px;color:var(--white);font-weight:600;font-size:22px;letter-spacing:.2px}
.brand-dot{width:14px;height:14px;border-radius:50%;background:var(--magenta)}
.site-header .brand{left:131px;top:22px}
.main-nav{position:absolute;top:24px;left:502px;display:flex;gap:0}
.main-nav a{color:var(--white);text-decoration:none;font-size:17px;font-weight:500;position:absolute;white-space:nowrap}
.main-nav a.active{color:var(--magenta);padding-bottom:5px;border-bottom:2px solid var(--magenta)}
.hero{position:absolute;top:75px;left:0;width:1200px;height:560px;
  background:radial-gradient(ellipse 300px 280px at 880px 300px,#2e4fe0 0%,#6b86f0 35%,rgba(210,210,225,0) 70%),
  linear-gradient(100deg,#5b5858 0%,#a9a6a8 25%,#d6d4d9 55%,#e4e3e8 100%)}
.hero h1{position:absolute;left:131px;top:207px;font-family:'Montserrat',sans-serif;font-weight:900;font-size:56px;line-height:64px;color:var(--white);letter-spacing:-.5px;text-shadow:0 2px 6px rgba(0,0,0,.25)}
.slider-dots{position:absolute;left:568px;top:523px;display:flex;gap:7px}
.slider-dots span{width:8px;height:8px;background:#151a2a}
.slider-dots span.on{background:var(--magenta)}
.partner-photo{position:absolute;left:132px;top:692px;width:468px;height:342px;
  background:linear-gradient(90deg,#6d7490 0%,#8d90a8 35%,#2c2f3a 60%,#1a2440 100%)}
.partner-text{position:absolute;left:641px;top:704px;width:428px}
.partner-text h2{color:var(--magenta);font-weight:900;font-size:23px;letter-spacing:.2px;font-family:'Montserrat',sans-serif}
.partner-text .lead{margin-top:14px;font-weight:800;font-size:14.5px;line-height:19px;color:var(--white)}
.partner-text p{margin-top:30px;font-size:15px;line-height:19.2px;text-align:justify;color:var(--white)}
.partner-text p + p{margin-top:19px}
.cta-box{position:absolute;left:264px;top:1098px;width:673px;height:41px;border:1px solid #8a90a3;display:flex;align-items:center;justify-content:center;font-weight:800;font-size:16px;color:var(--white)}
.offer-card{position:absolute;width:297px;background:var(--card);padding:22px 12px 0}
.offer-card.private{left:133px;top:1323px;height:560px}
.offer-card.business{left:453px;top:1180px;height:844px}
.offer-card.community{left:769px;top:1323px;height:560px}
.offer-icon{width:76px;height:76px;border-radius:50%;margin:0 auto;background:linear-gradient(160deg,#b62fd3,var(--magenta));display:flex;align-items:center;justify-content:center}
.offer-card h3{text-align:center;font-weight:900;font-size:15.5px;color:var(--white);margin-top:22px;letter-spacing:.2px}
.offer-list{list-style:none;margin-top:24px}
.offer-list li{position:relative;padding:7px 4px 7px 22px;font-size:12.5px;line-height:16px;border-bottom:1px solid var(--line);color:var(--white)}
.offer-list li:last-child{border-bottom:none}
.offer-list li::before{content:"";position:absolute;left:7px;top:12px;width:7px;height:7px;border-radius:50%;background:var(--magenta)}
.business .offer-list{margin-top:24px}
.sector-box{background:var(--card-inner);margin:4px -2px 8px;padding:10px 18px;list-style:none}
.sector-box li{font-size:12.5px;line-height:20px;color:var(--white)}
.site-footer{position:absolute;left:0;top:2070px;width:1200px;height:262px;background:var(--footer)}
.site-footer .brand{left:0;right:0;justify-content:center;top:45px;font-size:24px}
.footer-nav{position:absolute;top:105px;left:0;width:1200px;display:flex;justify-content:center;gap:30px}
.footer-nav a{color:var(--white);text-decoration:none;font-size:15.5px}
.social{position:absolute;top:151px;left:0;width:1200px;display:flex;justify-content:center;gap:17px}
.social span{width:33px;height:33px;border-radius:7px;background:var(--white)}
.copyright{position:absolute;top:222px;width:1200px;text-align:center;font-size:13px;color:var(--white)}
</style>
</head>
<body>
<header class="site-header">
  <div class="brand"><span class="brand-dot"></span>tanu-werk.de</div>
  <nav class="main-nav">
    <a class="active" href="#" style="left:0">Lösungen</a>
    <a href="#" style="left:124px">Unternehmen</a>
    <a href="#" style="left:281px">Services</a>
    <a href="#" style="left:393px">Karriere</a>
    <a href="#" style="left:503px">Kontakt</a>
  </nav>
</header>

<section class="hero" role="img" aria-label="Nahaufnahme eines Ladesteckers in einer blau leuchtenden Ladebuchse">
  <h1>EINFACH MEHR<br>ALS LADEN</h1>
  <div class="slider-dots"><span></span><span></span><span class="on"></span><span></span><span></span></div>
</section>

<div class="partner-photo" role="img" aria-label="Ladesäule mit eingestecktem Ladekabel vor unscharfem Lichterhintergrund"></div>
<section class="partner-text">
  <h2>TANU-WERK IST IHR PARTNER</h2>
  <p class="lead">wenn das Laden nicht nur einfach, sondern die Umsetzung auch aus einer Hand kommen soll</p>
  <p>Wir bieten Lösungen sowohl für Privatkunden, Geschäftskunden als auch Kommunen an, die schnell, fair und ohne Eigenleistung zu einer smarten Ladelösung für E-Fahrzeuge kommen möchten.</p>
  <p>Von der Beratung, über die Installation, Inbetriebnahme bis zur Abrechnung und Wartung bekommen Sie bei tanu-werk alles aus einer Hand. Auf Wunsch vermieten wir auch die Ladetechnik und übernehmen im gewerblichen Bereich die direkte Abrechnung mit dem Nutzer. Für Kommunen bieten wir den kostenfreien Full-Service an und beteiligen die Gemeinden an der Nutzung der Infrastruktur.</p>
</section>

<div class="cta-box">Fragen Sie uns nach der auf Ihre individuellen Bedürfnisse zugeschnittenen Lösung:</div>

<article class="offer-card private">
  <div class="offer-icon"><svg width="40" height="42" viewBox="0 0 40 42"><circle cx="20" cy="12" r="9" fill="#fff"/><path d="M3 42c0-11 7-17 17-17s17 6 17 17z" fill="#fff"/></svg></div>
  <h3>ALS PRIVATKUNDE</h3>
  <ul class="offer-list">
    <li>Bestandsanalyse mit umfangreicher Beratung über die Möglichkeiten der Umsetzung</li>
    <li>Prüfung und Übernahme der Anmeldung verfügbarer Fördermöglichkeiten</li>
    <li>Auswahl an smarten Wallbox Lösungen, passend für Ihr Fahrzeug und Ihre Bedürfnisse</li>
    <li>Installation inkl. aller notwendigen Materialien und Tätigkeiten (Durchbrüche, Erdarbeiten, etc.)</li>
    <li>Inbetriebnahme und Einweisung in die Ladetechnik</li>
    <li>Jährlich technische Wartung nach DGUV3</li>
    <li>Reparaturservice, unter Berücksichtigung der geltenden Garantie Ansprüche</li>
  </ul>
</article>

<article class="offer-card business">
  <div class="offer-icon"><svg width="40" height="42" viewBox="0 0 40 42"><circle cx="20" cy="12" r="9" fill="#fff"/><path d="M3 42c0-11 7-17 17-17s17 6 17 17z" fill="#fff"/><path d="M18 26h4l-1 4 2 10h-6l2-10z" fill="#d81f97"/></svg></div>
  <h3>ALS GESCHÄFTSKUNDE</h3>
  <ul class="offer-list">
    <li>Durchführung einer individuellen Bedarfsanalyse inkl. Ermittlung der Anforderungen für:</li>
  </ul>
  <ul class="sector-box">
    <li>Haus- und Immobilienverwaltungen</li>
    <li>Dienstleistungs- und Handelsunternehmen</li>
    <li>Hotel und Beherbergungsbetriebe</li>
    <li>Parkraum- und Parkhausbetreiber</li>
    <li>Tourismus, Sport- und Freizeiteinrichtungen</li>
  </ul>
  <ul class="offer-list" style="margin-top:0">
    <li>Planung und Projektierung des Installationsaufwands inkl. Materialverbrauch</li>
    <li>Leasing oder Kauf der Hardware</li>
    <li>Normgerechte Installation der Ladeinfrastruktur inkl. Durchbruch-, Brandschutz- und Erdarbeiten</li>
    <li>Bei Bestandsbauten Integration der Ladeinfrastruktur in die Gebäudesystemtechnik und ggf. Anpassung des Netzanschlusses</li>
    <li>Inbetriebnahme der Anlage inkl. Prüf- und Messprotokollen</li>
    <li>Wiederkehrende technische Prüfung der Anlage nach DGUV 3</li>
    <li>Austausch und Reparatur Service</li>
    <li>Unterstützung bei der mtl. Nutzungsabrechnung und Einbindung in Ihre vorhandene Abrechnungssysteme</li>
    <li>ODER direkte Abrechnung mit den Nutzern</li>
  </ul>
</article>

<article class="offer-card community">
  <div class="offer-icon"><svg width="42" height="40" viewBox="0 0 42 40"><path d="M21 2 3 11v3h36v-3z" fill="#fff"/><rect x="7" y="16" width="4" height="16" fill="#fff"/><rect x="15" y="16" width="4" height="16" fill="#fff"/><rect x="23" y="16" width="4" height="16" fill="#fff"/><rect x="31" y="16" width="4" height="16" fill="#fff"/><rect x="3" y="34" width="36" height="4" fill="#fff"/></svg></div>
  <h3>ALS KOMMUNE</h3>
  <ul class="offer-list">
    <li>Konzeptionierung möglicher Ladeinfrastrukturen innerhalb Ihrer Gemeinde</li>
    <li>Planung und Projektsteuerung inkl. sämtlicher behördlicher Genehmigungsverfahren und Beantragung von Fördermitteln</li>
    <li>Fachgerechte Installation und Inbetriebnahme</li>
    <li>Regelmäßige Wartung gemäß Vorschrif</li>
    <li>Reparatur und Kundenservice</li>
    <li>Direkte Abrechnung mit dem Nutzer</li>
    <li>Beteiligung der Gemeinde am Umsatz</li>
    <li>Möglichkeit der Integration von Bonusprogrammen, mit denen der lokale Einzelhandel beworben wird</li>
  </ul>
</article>

<footer class="site-footer">
  <div class="brand"><span class="brand-dot"></span>tanu-werk.de</div>
  <nav class="footer-nav">
    <a href="#">AGB</a><a href="#">Datenschutzerklärung</a><a href="#">Impressum</a><a href="#">Kontakt</a><a href="#">Karriere</a><a href="#">FAQs</a>
  </nav>
  <div class="social"><span></span><span></span><span></span></div>
  <p class="copyright">Copyright © 2022 All Rights Reserved</p>
</footer>
</body>
</html>
```